I need a SEO-friendly Wordpress website (making sure to style H1, H2, H3, etc correctly) for a Hawaii-based law firm called Meridian Crest Legal Group. Comparable websites include https://brvlaw.example/ and https://www.lomrit.example/ for design reference. The current copy on the TarnAdvocate.example website can be used.

```html
<!DOCTYPE html>
<html lang="en">
<head>
<meta charset="utf-8">
<title>Meridian Crest Legal Group | Divorce and Personal Injury Lawyers</title>
<link href="https://fonts.googleapis.com/css2?family=Montserrat:wght@400;500;600;700;800&family=Open+Sans:wght@400;600&display=swap" rel="stylesheet">
<style>
:root{
  --brand-red:#c8102e;
  --navy:#0e121c;
  --ink:#1b1b1b;
  --muted:#555;
  --card:#eeeef2;
  --blog-card:#e9e9e9;
  --white:#fff;
  --footer:#0f131b;
}
*{box-sizing:border-box;margin:0;padding:0}
html,body{width:1200px;height:2721px;overflow:hidden;background:var(--white)}
body{font-family:"Open Sans",Arial,sans-serif;color:var(--ink);position:relative}
.abs{position:absolute}
a{color:inherit;text-decoration:none}

/* header */
.site-header{left:0;top:0;width:1200px;height:97px}
.brand-name{left:141px;top:16px;font-family:"Montserrat",sans-serif;font-weight:500;font-size:32px;color:var(--brand-red);letter-spacing:.2px}
.brand-tagline{left:143px;top:61px;font-family:"Montserrat",sans-serif;font-size:12.5px;color:var(--ink)}
.header-phone{left:858px;top:29px;display:flex;align-items:center;gap:10px;font-family:"Montserrat",sans-serif;font-size:19px;color:var(--ink)}
.phone-ring{width:40px;height:40px;border:1px solid #bbb;border-radius:50%;display:flex;align-items:center;justify-content:center}

.main-nav{left:0;top:97px;width:1200px;height:40px;background:var(--brand-red)}
.main-nav ul{list-style:none;position:absolute;left:144px;top:0;height:40px;display:flex}
.main-nav li{height:40px;display:flex;align-items:center;font-family:"Montserrat",sans-serif;font-size:13px;color:var(--white)}
.main-nav li.active{background:var(--navy);width:133px;justify-content:center}

/* hero */
.hero{left:0;top:137px;width:1200px;height:478px;background:linear-gradient(180deg,#3a2016 0%,#6b3520 45%,#8a4526 70%,#5a2c1a 100%)}
.hero-text{left:0;width:1200px;text-align:center;color:var(--white);text-shadow:0 1px 3px rgba(0,0,0,.6)}
.hero-kicker{top:322px;font-family:"Montserrat",sans-serif;font-size:23px}
.hero-title{top:357px;font-family:"Montserrat",sans-serif;font-weight:800;font-size:32px;letter-spacing:-.3px}
.hero-sub{top:405px;font-family:"Montserrat",sans-serif;font-size:16.5px}
.hero-arrow{top:360px}

/* areas */
.section-title{left:0;width:1200px;text-align:center;font-family:"Montserrat",sans-serif;font-weight:700;font-size:33px;color:var(--brand-red)}
.practice-card{top:742px;width:218px;height:167px;background:var(--card);text-align:center;color:var(--brand-red);font-family:"Montserrat",sans-serif;font-size:16.5px;line-height:23px}
.practice-card svg{position:absolute;left:50%;top:22px;transform:translateX(-50%)}
.practice-card span{position:absolute;left:8px;right:8px;top:103px}

/* intro split */
.intro-photo{left:0;top:990px;width:600px;height:439px;background:linear-gradient(135deg,#3b3124 0%,#8d7a62 40%,#d9d3c8 65%,#6d5a46 100%)}
.intro-panel{left:600px;top:990px;width:600px;height:439px;background:var(--navy);color:var(--white)}
.intro-panel h2{position:absolute;left:53px;top:65px;width:420px;font-family:"Montserrat",sans-serif;font-weight:600;font-size:26px;line-height:40px;letter-spacing:.3px}
.intro-panel p{position:absolute;left:53px;top:199px;width:410px;font-size:13px;line-height:27px;color:#d8d8d8}
.read-more{position:absolute;left:53px;top:330px;width:106px;height:36px;background:var(--white);color:var(--brand-red);font-family:"Montserrat",sans-serif;font-size:12.5px;display:flex;align-items:center;justify-content:center}

/* blog */
.blog-card{top:1557px;width:440px;height:455px;background:var(--blog-card)}
.blog-thumb{position:absolute;left:0;top:0;width:440px;height:279px}
.blog-card h3{position:absolute;left:21px;top:297px;font-family:"Montserrat",sans-serif;font-weight:400;font-size:16.5px;color:var(--brand-red)}
.blog-date{position:absolute;left:21px;top:323px;font-family:"Montserrat",sans-serif;font-size:12px;color:var(--muted)}
.blog-card p{position:absolute;left:21px;top:350px;width:400px;font-size:9.5px;line-height:17.6px;color:#333}
.blog-card p a{color:var(--brand-red)}
.blog-arrow{top:1770px}

/* map + contact */
.map-area{left:0;top:2094px;width:1200px;height:531px;background:linear-gradient(90deg,#b7d3f2 0%,#dfe6ea 18%,#ececec 35%,#eeeeee 100%)}
.contact-box{left:144px;top:2268px;width:297px;height:184px;background:rgba(14,18,28,.93);color:var(--white)}
.contact-box h2{position:absolute;left:16px;top:14px;font-family:"Montserrat",sans-serif;font-weight:600;font-size:31px}
.contact-box ul{list-style:none;position:absolute;left:16px;top:68px;font-size:13.5px;line-height:17px}
.contact-box li{display:flex;gap:10px;margin-bottom:12px}
.contact-box li svg{flex:none;margin-top:2px}

/* footer */
.site-footer{left:0;top:2625px;width:1200px;height:96px;background:var(--footer);color:#9a9ea6;font-size:10.5px}
.footer-links{position:absolute;left:144px;top:26px}
.footer-copy{position:absolute;left:144px;top:55px}
.social{position:absolute;top:28px;width:16px;height:16px;border-radius:50%;background:#8a8f98}
</style>
</head>
<body>

<header class="site-header abs">
  <a class="brand-name abs" href="#">Meridian Crest Legal Group</a>
  <div class="brand-tagline abs">DIVORCE AND PERSONAL INJURY LAWYERS</div>
  <div class="header-phone abs">
    <span class="phone-ring"><svg width="16" height="16" viewBox="0 0 24 24"><path fill="#1b1b1b" d="M6.6 10.8c1.4 2.8 3.8 5.1 6.6 6.6l2.2-2.2c.3-.3.7-.4 1-.2 1.1.4 2.3.6 3.6.6.6 0 1 .4 1 1V20c0 .6-.4 1-1 1C10.6 21 3 13.4 3 4c0-.6.4-1 1-1h3.5c.6 0 1 .4 1 1 0 1.3.2 2.5.6 3.6.1.3 0 .7-.2 1z"/></svg></span>
    +1.808.555.0148
  </div>
</header>

<nav class="main-nav abs">
  <ul>
    <li class="active">HOME</li>
    <li style="width:199px;justify-content:center">PRACTICE AREAS</li>
    <li style="width:232px;justify-content:center">ATTORNEYS</li>
    <li style="width:116px;justify-content:center">BLOG</li>
    <li style="width:240px;justify-content:center">CONTACT US</li>
  </ul>
</nav>

<section class="hero abs" role="img" aria-label="Wood-panelled courtroom with judge's bench and gallery seating"></section>
<p class="hero-text hero-kicker abs">OVER 70 YEARS OF COMBINED PRACTICE, SPECIALIZING IN:</p>
<h1 class="hero-text hero-title abs">PERSONAL INJURY, FAMILY &amp; DIVORCE CHILD CUSTODY</h1>
<p class="hero-text hero-sub abs">Dedicated to making sure you receive the care and attention you need.</p>
<svg class="hero-arrow abs" style="left:54px" width="18" height="30" viewBox="0 0 18 30"><path d="M15 3 4 15l11 12" fill="none" stroke="#fff" stroke-width="3.5"/></svg>
<svg class="hero-arrow abs" style="left:1126px" width="18" height="30" viewBox="0 0 18 30"><path d="M3 3l11 12L3 27" fill="none" stroke="#fff" stroke-width="3.5"/></svg>

<h2 class="section-title abs" style="top:685px">AREAS OF PRACTICE</h2>

<div class="practice-card abs" style="left:144px">
  <svg width="86" height="72" viewBox="0 0 86 72"><path d="M43 68 8 34C-2 23 4 4 21 4c10 0 16 6 22 13 6-7 12-13 22-13 17 0 23 19 13 30z" fill="none" stroke="#c8102e" stroke-width="4"/><path d="M43 17 36 32l10 8-8 14 5 14" fill="none" stroke="#c8102e" stroke-width="4"/></svg>
  <span>Family &amp; Divorce</span>
</div>
<div class="practice-card abs" style="left:376px">
  <svg width="56" height="72" viewBox="0 0 56 72"><circle cx="28" cy="18" r="12" fill="none" stroke="#c8102e" stroke-width="3"/><path d="M4 70V50c0-9 8-15 16-15h16c8 0 16 6 16 15v20z" fill="none" stroke="#c8102e" stroke-width="3"/><path d="M14 70V54M42 70V54M20 44l16 16M36 44 20 60" stroke="#c8102e" stroke-width="3"/></svg>
  <span>Personal Injury</span>
</div>
<div class="practice-card abs" style="left:607px">
  <svg width="64" height="72" viewBox="0 0 64 72"><path d="M32 14c-11 0-18 8-18 18 0 8 6 12 8 20h20c2-8 8-12 8-20 0-10-7-18-18-18z" fill="none" stroke="#c8102e" stroke-width="3"/><path d="M23 58h18M25 64h14M32 2v6M8 12l5 5M56 12l-5 5M2 32h6M56 32h6" stroke="#c8102e" stroke-width="3"/></svg>
  <span>Corporate &amp; Intellectual Property</span>
</div>
<div class="practice-card abs" style="left:838px">
  <svg width="68" height="72" viewBox="0 0 68 72"><path d="M4 70V34h14V12h10V2h12v10h10v22h14v36z" fill="none" stroke="#c8102e" stroke-width="3"/><path d="M10 42h4M10 50h4M10 58h4M54 42h4M54 50h4M54 58h4M24 22h20M24 32h20M24 42h20M24 52h20M24 62h20" stroke="#c8102e" stroke-width="3"/></svg>
  <span>Real Estate</span>
</div>

<div class="intro-photo abs" role="img" aria-label="Lawyer handing a document to a client across a desk with a gavel and law books"></div>
<section class="intro-panel abs">
  <h2>LAWYERS SERVING THE BIG ISLAND AND NEIGHBORING ISLANDS</h2>
  <p>The experienced attorneys in the Meridian Crest Legal Group's Kailua Kona, Hawaii office provide clients with a wide range of litigation expertise, including legal claims involving divorce &amp; family, personal injury, toxic exposures, intellectual property, and real estate.</p>
  <a class="read-more" href="#">READ MORE</a>
</section>

<h2 class="section-title abs" style="top:1500px">BLOG</h2>
<svg class="blog-arrow abs" style="left:55px" width="14" height="26" viewBox="0 0 14 26"><path d="M12 2 2 13l10 11" fill="none" stroke="#888" stroke-width="3"/></svg>
<svg class="blog-arrow abs" style="left:1129px" width="14" height="26" viewBox="0 0 14 26"><path d="M2 2l10 11L2 24" fill="none" stroke="#888" stroke-width="3"/></svg>

<article class="blog-card abs" style="left:144px">
  <div class="blog-thumb" role="img" aria-label="Attorney in a vest signing paperwork beside stacked files" style="background:linear-gradient(135deg,#d8d8d6 0%,#2a2a2e 45%,#6b6a68 75%,#c9c6c0 100%)"></div>
  <h3>Top 10 Things to Do Before Filing for Divorce</h3>
  <div class="blog-date">2 July, 2019</div>
  <p>No one gets married with the intention of things not working out, but it's an unfortunate fact that many marriages don't work out in the end. For those who are in troubled marriage, here are the Top 10 things you should do before filing for a divorce... <a href="#">[continue reading]</a></p>
</article>
<article class="blog-card abs" style="left:616px">
  <div class="blog-thumb" role="img" aria-label="Mother and daughter reading a book together on a sofa" style="background:linear-gradient(135deg,#aebfcf 0%,#e7c7b6 40%,#e8a4b0 70%,#f0ece6 100%)"></div>
  <h3>Top 15 Things to Do During Custody Battle</h3>
  <div class="blog-date">2 July, 2019</div>
  <p>It's already tragic enough when two people who planned on spending their lives together no longer wish to see that dream through, but to compound the tragedy is when children [and their custody] get caught in the crossfire. With that in mind, here are the top 15 things you can do to make this difficult time go as smoothly as possible, and with minimal strain put on your children... <a href="#">[continue reading]</a></p>
</article>

<div class="map-area abs" role="img" aria-label="Street map of Kailua Kona showing the office location"></div>
<section class="contact-box abs">
  <h2>CONTACT INFO</h2>
  <ul>
    <li><svg width="10" height="14" viewBox="0 0 10 14"><path d="M5 0a5 5 0 0 0-5 5c0 4 5 9 5 9s5-5 5-9a5 5 0 0 0-5-5zm0 7a2 2 0 1 1 0-4 2 2 0 0 1 0 4z" fill="#fff"/></svg><span>64-2180 Lanai Ridge Road, Suite 212<br>Kailua Kona, Hawaii 96745</span></li>
    <li><svg width="12" height="12" viewBox="0 0 24 24"><path fill="#fff" d="M6.6 10.8c1.4 2.8 3.8 5.1 6.6 6.6l2.2-2.2c.3-.3.7-.4 1-.2 1.1.4 2.3.6 3.6.6.6 0 1 .4 1 1V20c0 .6-.4 1-1 1C10.6 21 3 13.4 3 4c0-.6.4-1 1-1h3.5c.6 0 1 .4 1 1 0 1.3.2 2.5.6 3.6.1.3 0 .7-.2 1z"/></svg><span>Phone: +1.808.555.0148</span></li>
    <li><svg width="12" height="12" viewBox="0 0 12 12"><path d="M0 2h12v8H0z" fill="#fff"/><path d="M0 2l6 5 6-5" fill="none" stroke="#0e121c" stroke-width="1.2"/></svg><span>Email : clients@tarnadvocate.example</span></li>
  </ul>
</section>

<footer class="site-footer abs">
  <div class="footer-links">Home &nbsp;|&nbsp; Practice Areas &nbsp;|&nbsp; Attorneys &nbsp;|&nbsp; Blog &nbsp;|&nbsp; Contact US</div>
  <div class="footer-copy">Copyright &copy; 2019 &nbsp;Meridian Crest Legal Group. &nbsp;&nbsp;All rights reserved.</div>
  <span class="social" style="left:964px"></span>
  <span class="social" style="left:999px"></span>
  <span class="social" style="left:1038px"></span>
</footer>

</body>
</html>
```